eBook-Cover für Thriller gesucht
An dieser Stelle ein großes Lob und vielen Dank an die Designerin Larosa. Auch das zweite Buchcover ist wieder überaus gelungen, eine ganz tolle Arbeit. Auch die angenehme Zusammenarbeit war mir, wie schon beim ersten Auftrag, eine Freude. Ebenso hervorzuheben ist die Schnelligkeit und Kreativität, mit der die Designerin auf Änderungswünsche reagiert. Als Auftraggeber gebe ich verdiente fünf Sterne und bin mit dem Ergebnis wirklich sehr zufrieden.
Zielgruppe
Ich bin Autor. Zielgruppe sind (anspruchsvolle) Leser/innen von Thrillern und Kriminalromanen im ebook-Bereich.
Aufgabenstellung
- Gesucht wird ein ebook-Cover für einen Thriller mit dem Titel 'Kaltgrund'
- Grobe Aufteilung siehe Skizzen
- Fokus des Covers liegt auf dem Buchtitel und dem Motiv ('Blauer Drachen')
- Hintergrund eher hell, Assoziation mit zarter Eisfläche mit angedeuteten Rissen vom Hauptmotiv ausgehend. Dadurch auch Tiefe und Dreidimensionalität. (Beispiel zum Hintergrund: 'Schattenfrist' von Heinrich Wendel, jedoch ohne Blut )
-Titelschrift groß, Stil 'gekratzt' bzw. 'gestrichelt', (Schriftart ähnlich wie Autorenname bei 'Die Schleuse' von Matthias Kolbe). Schrift groß und 'treppenförmig' neben dem Hauptmotiv angeordnet. Schriftfarbe schwarz/dunkelblau, ähnlich Hauptmotiv (Bsp.: 'Schwarzeid' von Heinrich Wendel)
Hauptmotiv ist der vom rechten Coverrand hineinragende 'Blaue Drachen' (Glaucus atlanticus, siehe hochgeladenes Beispielbild von Wissnetz)
- Schriftart von Autorenname und Genre eher klar
- eigene Detailvorschläge zur Optimierung des Ergebnisses möglich bzw. erwünscht

```html
<!DOCTYPE html>
<html lang="de">
<head>
<meta charset="utf-8">
<title>Kaltgrund – Thriller</title>
<link rel="stylesheet" href="https://fonts.googleapis.com/css2?family=Barlow:wght@400&family=Rubik+Distressed&display=swap">
<style>
  :root {
    --ice-light: #f2f9fd;
    --ice-mid: #cfe7f3;
    --ice-deep: #8fc3df;
    --crack: #5d93b5;
    --ink: #0e2a57;
    --author: #2f5f93;
    --genre: #2c5a8c;
    --dragon-core: #1c2f6e;
  }
  * { margin: 0; padding: 0; box-sizing: border-box; }
  html, body { width: 750px; height: 1200px; overflow: hidden; background: var(--ice-light); }
  .cover {
    position: relative;
    width: 750px;
    height: 1200px;
    overflow: hidden;
    background:
      radial-gradient(ellipse 420px 300px at 30% 20%, rgba(255,255,255,0.85), transparent 70%),
      radial-gradient(ellipse 380px 420px at 70% 60%, rgba(255,255,255,0.7), transparent 70%),
      radial-gradient(ellipse 500px 400px at 0% 80%, var(--ice-deep), transparent 70%),
      radial-gradient(ellipse 400px 300px at 100% 0%, var(--ice-deep), transparent 70%),
      linear-gradient(160deg, var(--ice-mid), var(--ice-light) 45%, var(--ice-mid));
  }
  .ice-cracks, .type-layer { position: absolute; inset: 0; width: 750px; height: 1200px; }
  .ice-cracks path { fill: none; stroke: var(--crack); stroke-linecap: round; stroke-linejoin: round; opacity: 0.55; }
  .motif-dragon {
    position: absolute;
    left: 240px;
    top: 250px;
    width: 470px;
    height: 480px;
    border-radius: 48% 40% 52% 44%;
    background: radial-gradient(ellipse at 55% 40%, var(--dragon-core) 0%, rgba(60,100,180,0.55) 40%, rgba(111,154,214,0.15) 70%, transparent 78%);
  }
  .author {
    font-family: "Barlow", sans-serif;
    font-weight: 400;
    font-size: 90px;
    fill: var(--author);
  }
  .title {
    font-family: "Rubik Distressed", sans-serif;
    font-size: 250px;
    fill: var(--ink);
    filter: drop-shadow(3px 4px 4px rgba(14,42,87,0.35));
  }
  .genre {
    font-family: "Barlow", sans-serif;
    font-weight: 400;
    font-size: 44px;
    fill: var(--genre);
  }
</style>
</head>
<body>
  <main class="cover">
    <svg class="ice-cracks" viewBox="0 0 750 1200" aria-hidden="true">
      <path d="M480 520 L470 430 L488 330 L500 240 L540 150 L560 60" stroke-width="2"/>
      <path d="M420 560 L330 520 L250 470 L170 480 L80 440" stroke-width="1.5"/>
      <path d="M300 700 L250 760 L230 840 L210 900 L150 990 L90 1040 L50 1130" stroke-width="2.5"/>
      <path d="M230 840 L170 820 L90 850 L20 830" stroke-width="1.2"/>
      <path d="M560 600 L620 520 L700 470 L750 460" stroke-width="1.2"/>
      <path d="M510 170 L600 120 L680 140" stroke-width="1"/>
      <path d="M150 990 L70 1000 L0 1020" stroke-width="1"/>
    </svg>

    <div class="motif-dragon" role="img" aria-label="Blauer Drache (Glaucus atlanticus), dunkelblaue Meeresschnecke mit gefächerten Armen auf der Eisfläche"></div>

    <svg class="type-layer" viewBox="0 0 750 1200">
      <text class="author" x="46" y="148" textLength="664" lengthAdjust="spacingAndGlyphs">TOBIAS LENHARDT</text>
      <g role="heading" aria-level="1" aria-label="Kaltgrund">
        <text class="title" x="29" y="491" textLength="338" lengthAdjust="spacingAndGlyphs" aria-hidden="true">KAL</text>
        <text class="title" x="141" y="793" textLength="305" lengthAdjust="spacingAndGlyphs" aria-hidden="true">TGR</text>
        <text class="title" x="436" y="917" textLength="278" lengthAdjust="spacingAndGlyphs" aria-hidden="true">UND</text>
      </g>
      <text class="genre" x="268" y="1110" textLength="220" lengthAdjust="spacingAndGlyphs">THRILLER</text>
    </svg>
  </main>
</body>
</html>
```